Online Training company needs a new website design (Wordpress)

We are looking for a new design for our website (run on WordPress). We currently have two websites (quizbrightly.com) and (velmoracademy.com) and are trying to combine them into a single design.

The site should contain the following sections (Start Here, courses, labs, practice exams, exam vouchers, books, articles, about us).

Start Here - With so many options on our site, we think it would be a good idea to have this page that will allow us to give students an overview of our different products/services and where to start when they first find out about our company.

Courses - These are our online video courses (products), currently hosted at velmoracademy.com. Each course has its own "product page".

Labs - These are online lab environments that a student can purchase. The layout for these would be similar to a course, but the purchase option will be different (our web developer will code all the back end stuff to make it work).

Practice Exams - This will allow students to take practice questions to study for their exams.

Exam Vouchers - Students can purchase their exam vouchers here at a discounted price for their certification exams.

Books - Will link to a page that displays our books that are available on Brixly. (Examples of the covers are attached so you can see our current designs.)

Articles - This will be our "blog" area for us to post articles each week.

About Us - A short about us page describing our company.

***
As for the design of the page itself, we like the current color scheme at velmoracademy.com, but the layout isn't working well. It was fine when we just had video courses, but as we have added new products it is becoming more and more cumbersome.

I have been looking for inspiration around the web, and saw quietharvestplan.com as a good example of trying to provide focus to new users, while breaking out various parts of a business that contains 4-6 different product lines/topics. Another example of a site we like is lessonlanternhub.com.

That said, we aren't looking to simply copy either site, and are completely open to recommendations and designs you may have.

Thank you and we look forward to working with you!

```html
<!DOCTYPE html>
<html lang="en">
<head>
<meta charset="utf-8">
<title>Velmor Academy – Online Training</title>
<link href="https://fonts.googleapis.com/css2?family=Montserrat:wght@400;600;700;800&family=Open+Sans:wght@400;600;700&display=swap" rel="stylesheet">
<style>
:root{
  --blue:#3a6b9f;
  --blue-dark:#2c5687;
  --blue-light:#5f8fc2;
  --navy:#1f3550;
  --ink:#2b2b2b;
  --muted:#6b6b6b;
  --white:#ffffff;
  --footer:#151515;
  --line:#e3e8ee;
}
*{box-sizing:border-box;margin:0;padding:0}
html,body{width:1200px;height:4688px;overflow:hidden}
body{font-family:"Open Sans",Arial,sans-serif;color:var(--ink);background:var(--white);position:relative}
h1,h2,h3,h4,.brand,.btn,.nav a{font-family:"Montserrat",Arial,sans-serif}
section,header,footer{position:absolute;left:0;width:1200px}
.abs{position:absolute}
.btn{display:inline-flex;align-items:center;justify-content:center;border-radius:30px;font-weight:700;font-size:15px;letter-spacing:.5px;color:var(--white);background:var(--blue);text-transform:uppercase}
.section-title{position:absolute;left:0;width:1200px;text-align:center;font-size:42px;font-weight:700;text-transform:uppercase;letter-spacing:1px}

/* header */
.site-header{top:0;height:103px;background:var(--white)}
.topbar{position:absolute;right:0;top:0;width:575px;height:32px;background:var(--blue);border-bottom-left-radius:16px;display:flex;align-items:center;gap:14px;padding-left:30px;color:var(--white);font-size:13px}
.topbar .dot{width:20px;height:20px;border-radius:50%;background:var(--white);opacity:.9}
.topbar .sep{flex:1}
.topbar span{display:flex;align-items:center;gap:6px}
.logo{position:absolute;left:78px;top:16px;display:flex;align-items:center;gap:12px}
.logo .mark{width:58px;height:58px;border-radius:50%;background:var(--blue)}
.brand{font-weight:800;font-size:26px;line-height:26px;color:var(--blue-dark);text-transform:uppercase}
.nav{position:absolute;left:344px;top:58px;display:flex;gap:26px;align-items:center}
.nav a{color:var(--ink);text-decoration:none;font-size:16px;font-weight:600}

/* hero */
.hero{top:103px;height:569px;background:linear-gradient(100deg,#eef0f1 0%,#e2e0dc 38%,#cfc6bb 62%,#b9aea2 100%)}
.hero h1{position:absolute;left:78px;top:190px;font-size:48px;font-weight:800;line-height:54px;color:var(--navy);text-transform:uppercase}
.hero h1 em{font-style:normal;color:var(--blue-light)}
.hero .btn{position:absolute;left:78px;top:372px;width:238px;height:58px}
.slider-dots{position:absolute;right:20px;top:225px;display:flex;flex-direction:column;gap:14px}
.slider-dots i{width:12px;height:12px;border-radius:50%;background:var(--white);opacity:.6}
.slider-dots i:first-child{opacity:1}

/* features */
.features{top:672px;height:250px;background:var(--blue)}
.feature{position:absolute;top:-50px;width:240px;text-align:center;color:var(--white)}
.feature .icon{width:104px;height:104px;margin:0 auto;border-radius:50%;background:var(--white);display:flex;align-items:center;justify-content:center}
.feature h3{font-size:20px;font-weight:700;margin-top:20px;text-transform:uppercase}
.feature p{font-size:13px;line-height:20px;margin-top:8px;padding:0 14px;opacity:.95}

/* about */
.about{top:922px;height:428px;background:var(--white)}
.about h2{position:absolute;left:78px;top:80px;font-size:44px;font-weight:700;color:var(--blue-dark)}
.about p{position:absolute;left:78px;width:520px;font-size:14px;line-height:24px;color:var(--muted)}
.about .btn{position:absolute;left:78px;top:310px;width:182px;height:52px}
.about .device{position:absolute;left:655px;top:30px;width:455px;height:365px;border-radius:26px;background:linear-gradient(160deg,#4b4f55 0%,#2a2d31 55%,#cfd3d7 100%)}

/* courses */
.courses{top:1350px;height:619px;background:linear-gradient(180deg,#1e2a38 0%,#2b3746 50%,#1c2530 100%)}
.courses .section-title{top:55px;color:var(--blue-light)}
.course{position:absolute;top:134px;height:382px;background:var(--white);border-radius:10px;overflow:hidden}
.course .thumb{height:188px;margin:10px;border-radius:6px}
.course .price{position:absolute;left:10px;top:198px;padding:0 18px;height:38px;line-height:38px;background:var(--blue);color:var(--white);font-family:"Montserrat",sans-serif;font-weight:700;font-size:17px;border-top-right-radius:18px;border-bottom-right-radius:18px}
.course h4{position:absolute;left:22px;top:250px;font-size:16px;font-weight:700;color:var(--ink)}
.course p{position:absolute;left:22px;right:22px;top:278px;font-size:12px;line-height:19px;color:var(--muted)}
.course .more{position:absolute;right:22px;bottom:18px;font-family:"Montserrat",sans-serif;font-weight:700;font-size:13px;color:var(--blue-dark);display:flex;align-items:center;gap:8px}
.course .more::before{content:"";position:absolute;left:0;right:0;bottom:-4px;height:2px;background:var(--blue-dark)}
.carousel-bars{position:absolute;top:542px;left:0;width:1200px;display:flex;justify-content:center;gap:10px}
.carousel-bars i{width:26px;height:4px;background:var(--white);opacity:.4}
.carousel-bars i:first-child{opacity:1}

/* students */
.students{top:1969px;height:640px;background:linear-gradient(180deg,#3f72a6 0%,#3a6b9f 100%)}
.students .section-title{top:62px;color:var(--white)}
.students p{position:absolute;left:200px;width:800px;text-align:center;color:var(--white);font-size:14px;line-height:24px}
.students .btn{position:absolute;top:250px;height:46px;background:transparent;border:2px solid var(--white);font-size:15px}
.students .photo{position:absolute;left:406px;top:328px;width:470px;height:298px;border-radius:6px;background:radial-gradient(ellipse at 50% 60%,#d9d4cf 0%,#8a8f96 55%,rgba(58,107,159,0) 80%)}

/* articles */
.articles{top:2609px;height:625px;background:var(--white)}
.articles .section-title{top:70px;color:var(--blue-dark)}
.feature-post{position:absolute;left:78px;top:132px;width:578px;height:437px;background:var(--blue);overflow:hidden}
.feature-post .thumb{height:281px;background:linear-gradient(150deg,#c1c8cf 0%,#4e5b69 55%,#2d3946 100%)}
.feature-post h4{position:absolute;left:22px;top:300px;font-size:16px;font-weight:700;color:var(--white);text-transform:uppercase}
.feature-post .date{position:absolute;left:22px;top:330px;font-size:13px;color:var(--white);display:flex;align-items:center;gap:8px}
.feature-post p{position:absolute;left:22px;top:360px;width:440px;font-size:13px;line-height:21px;color:var(--white)}
.feature-post .more{position:absolute;right:24px;bottom:16px;font-size:13px;font-weight:700;color:var(--white);border-bottom:2px solid var(--white)}
.post{position:absolute;left:688px;width:440px;height:92px}
.post .day{position:absolute;left:0;top:0;width:48px;height:82px;background:var(--navy);color:var(--white);text-align:center}
.post .day b{display:block;font-family:"Montserrat",sans-serif;font-size:26px;line-height:50px;font-weight:700}
.post .day small{display:block;background:var(--blue);font-size:12px;line-height:32px}
.post h4{position:absolute;left:64px;top:2px;font-size:16px;font-weight:700;color:var(--blue-dark);text-transform:uppercase}
.post p{position:absolute;left:64px;top:28px;width:340px;font-size:12px;line-height:18px;color:var(--muted)}
.articles .next{position:absolute;left:886px;top:545px}

/* stats */
.stats{top:3234px;height:328px;background:linear-gradient(100deg,#18222e 0%,#2b3847 45%,#3c4a59 70%,#1c2631 100%)}
.stat{position:absolute;top:72px;width:200px;text-align:center;color:var(--white)}
.stat .icon{width:84px;height:84px;margin:0 auto;border-radius:50%;border:2px solid rgba(255,255,255,.45);display:flex;align-items:center;justify-content:center}
.stat b{display:block;font-family:"Montserrat",sans-serif;font-size:30px;font-weight:700;margin-top:26px}
.stat span{display:block;font-size:13px;margin-top:4px;opacity:.85}

/* books */
.books{top:3562px;height:422px;background:var(--white)}
.books .section-title{top:52px;color:var(--blue-dark)}
.book-cover{position:absolute;left:312px;top:125px;width:235px;height:282px;background:linear-gradient(90deg,#2d5b8e 0%,#3a6b9f 12%,#f4f6f9 22%,#e9eef4 100%);box-shadow:6px 6px 16px rgba(0,0,0,.25)}
.book-info{position:absolute;left:572px;top:165px}
.book-info h3{font-size:20px;font-weight:700;color:var(--blue-dark);text-transform:uppercase}
.book-info p{font-size:14px;line-height:22px;color:var(--muted);margin-top:10px;width:300px}
.book-info .store{font-family:"Open Sans",sans-serif;font-weight:700;font-size:30px;color:var(--ink);margin-top:20px;display:block}
.book-info .btn{width:163px;height:48px;margin-top:18px}

/* member */
.member{top:3984px;height:375px;background:var(--blue)}
.member .section-title{top:88px;color:var(--white);font-size:40px}
.member p{position:absolute;left:180px;width:840px;text-align:center;color:var(--white);font-size:14px;line-height:24px}
.signup{position:absolute;left:265px;top:210px;width:673px;height:52px;background:var(--white);border-radius:26px;display:flex;align-items:center;padding:0 8px 0 26px;justify-content:space-between;font-size:13px;color:var(--muted)}
.signup .go{width:40px;height:40px;border-radius:50%;background:var(--blue);display:flex;align-items:center;justify-content:center}

/* footer */
.site-footer{top:4359px;height:329px;background:var(--footer);color:#bdbdbd}
.site-footer .logo{left:78px;top:72px}
.site-footer .brand{color:var(--white)}
.site-footer .copy{position:absolute;left:78px;top:184px;font-size:12px;line-height:19px;color:#bdbdbd}
.foot-col{position:absolute;top:40px}
.foot-col h4{font-size:15px;font-weight:700;color:var(--blue-light);text-transform:uppercase;margin-bottom:12px}
.foot-col li{list-style:none;font-size:12px;line-height:27px}
.foot-col li::before{content:"› ";color:var(--blue-light)}
.contact-line{display:flex;gap:10px;align-items:flex-start;font-size:12px;line-height:20px;margin-bottom:10px}
.socials{display:flex;gap:10px;margin-top:6px}
.socials i{width:30px;height:30px;border-radius:50%;background:var(--blue)}
.foot-col p{font-size:12px;line-height:20px;width:260px}
.foot-col .btn{width:164px;height:46px;margin-top:24px;font-size:14px}
</style>
</head>
<body>

<header class="site-header">
  <div class="topbar">
    <span>Follow Us</span><i class="dot"></i><i class="dot"></i><i class="dot"></i>
    <span class="sep"></span>
    <span>
      <svg width="14" height="14" viewBox="0 0 24 24"><path fill="#fff" d="M6.6 10.8a15 15 0 0 0 6.6 6.6l2.2-2.2c.3-.3.7-.4 1-.2 1.1.4 2.3.6 3.6.6.6 0 1 .4 1 1V20c0 .6-.4 1-1 1A17 17 0 0 1 3 4c0-.6.4-1 1-1h3.5c.6 0 1 .4 1 1 0 1.3.2 2.5.6 3.6.1.3 0 .7-.2 1z"/></svg>
      Contact Us</span>
    <span>
      <svg width="14" height="14" viewBox="0 0 24 24"><circle cx="12" cy="8" r="4" fill="#fff"/><path fill="#fff" d="M4 21c0-4 4-6 8-6s8 2 8 6z"/></svg>
      Sign In</span>
    <span style="width:18px"></span>
  </div>
  <div class="logo"><div class="mark"></div><div class="brand">Velmor<br>Academy</div></div>
  <nav class="nav">
    <svg width="16" height="16" viewBox="0 0 24 24"><path fill="#3a6b9f" d="M12 3 2 12h3v8h5v-5h4v5h5v-8h3z"/></svg>
    <a>Start Here</a><a>Courses</a><a>Labs</a><a>Practice Exams</a><a>Exams Vouchers</a><a>Book</a><a>Articles</a><a>About Us</a>
  </nav>
</header>

<section class="hero">
  <div class="abs" role="img" aria-label="Photo of a student studying on a laptop on a sofa" style="left:600px;top:0;width:600px;height:569px;background:linear-gradient(90deg,rgba(226,224,220,0) 0%,rgba(150,130,112,.35) 60%,rgba(120,104,90,.25) 100%)"></div>
  <h1>We are engaged to<br>give you a<br><em>good future</em></h1>
  <a class="btn">Get Started Today</a>
  <div class="slider-dots"><i></i><i></i><i></i></div>
</section>

<section class="features">
  <div class="feature" style="left:83px">
    <div class="icon"><svg width="50" height="44" viewBox="0 0 50 44"><rect x="3" y="3" width="44" height="30" rx="3" fill="none" stroke="#3a6b9f" stroke-width="3"/><path d="M21 11v14l12-7z" fill="#3a6b9f"/><path d="M15 40h20" stroke="#3a6b9f" stroke-width="3"/></svg></div>
    <h3>Videos</h3>
    <p>Using our Quiz Brightly video series, we take complicated certification exams...</p>
  </div>
  <div class="feature" style="left:342px">
    <div class="icon"><svg width="44" height="46" viewBox="0 0 44 46"><rect x="6" y="3" width="32" height="40" rx="2" fill="none" stroke="#3a6b9f" stroke-width="3"/><path d="M13 13h18M13 20h18M13 27h12" stroke="#3a6b9f" stroke-width="3"/></svg></div>
    <h3>Books</h3>
    <p>Our Quiz Brightly book series will get you certified in the shortest amount of time.</p>
  </div>
  <div class="feature" style="left:605px">
    <div class="icon"><svg width="34" height="50" viewBox="0 0 34 50"><rect x="3" y="3" width="28" height="44" rx="4" fill="none" stroke="#3a6b9f" stroke-width="3"/><circle cx="17" cy="40" r="2.5" fill="#3a6b9f"/><path d="M10 12h14M10 19h14M10 26h14" stroke="#3a6b9f" stroke-width="3"/></svg></div>
    <h3>Apps</h3>
    <p>Our quiz apps prepare you for the certification exam while on the go. Each question.</p>
  </div>
  <div class="feature" style="left:874px">
    <div class="icon"><svg width="46" height="44" viewBox="0 0 46 44"><rect x="3" y="3" width="34" height="38" rx="3" fill="#3a6b9f"/><path d="M37 12h6v26a3 3 0 0 1-6 0" fill="none" stroke="#3a6b9f" stroke-width="3"/><path d="M10 12h20M10 20h20M10 28h14" stroke="#fff" stroke-width="3"/></svg></div>
    <h3>Blog</h3>
    <p>Signup for your daily dose of training with our constantly updated blog feed.</p>
  </div>
</section>

<section class="about">
  <h2>ABOUT US</h2>
  <p style="top:146px">Marcus Ellery is an assistant professor and instructor at multiple universities and colleges. He has trained thousands of students across the globe in his cyber security and information technology courses.</p>
  <p style="top:236px">He holds numerous information technology professional certifications including Certified Systems Defense Professional (CSDP), Certified Ethical Tester (CET).</p>
  <a class="btn">Learn More</a>
  <div class="device" role="img" aria-label="Tablet on a stand showing the Velmor Academy name"></div>
</section>

<section class="courses" role="region" aria-label="Courses over a dimmed photo of a workspace">
  <h2 class="section-title">Courses</h2>
  <article class="course" style="left:78px;width:328px">
    <div class="thumb" role="img" aria-label="Collage of course covers" style="background:linear-gradient(135deg,#8fa9c6 0%,#3a6b9f 50%,#c7d4e2 100%)"></div>
    <span class="price">$9 / month</span>
    <h4>Full Access to All Our Courses</h4>
    <p>With our $9/month plan, you get unlimited access to all of our courses!</p>
    <span class="more">VIEW BUNDLE <svg width="16" height="12" viewBox="0 0 16 12"><path d="M0 6h13M9 1l5 5-5 5" stroke="#2c5687" stroke-width="2.4" fill="none"/></svg></span>
  </article>
  <article class="course" style="left:444px;width:322px">
    <div class="thumb" role="img" aria-label="Course cover on a dark circuit background" style="background:linear-gradient(135deg,#2e3a52 0%,#1d2636 60%,#3b4a66 100%);display:flex;align-items:center;justify-content:center"><span style="width:90px;height:90px;background:#fff;border-radius:8px"></span></div>
    <span class="price">$299</span>
    <h4>ServiceCore Foundation</h4>
    <p>Purchase your discounted ServiceCore Foundation exam voucher directly from Velmor Academy.</p>
    <span class="more">VIEW BUNDLE <svg width="16" height="12" viewBox="0 0 16 12"><path d="M0 6h13M9 1l5 5-5 5" stroke="#2c5687" stroke-width="2.4" fill="none"/></svg></span>
  </article>
  <article class="course" style="left:803px;width:316px">
    <div class="thumb" role="img" aria-label="Course cover on a blue background" style="background:linear-gradient(135deg,#2f5d93 0%,#4b7db3 60%,#28507e 100%);display:flex;align-items:center;justify-content:center"><span style="width:90px;height:90px;background:#fff;border-radius:8px"></span></div>
    <span class="price">$299</span>
    <h4>ProjectPath Foundation</h4>
    <p>Purchase your discounted ProjectPath Foundation exam voucher directly.</p>
    <span class="more">VIEW BUNDLE <svg width="16" height="12" viewBox="0 0 16 12"><path d="M0 6h13M9 1l5 5-5 5" stroke="#2c5687" stroke-width="2.4" fill="none"/></svg></span>
  </article>
  <div class="carousel-bars"><i></i><i></i><i></i></div>
</section>

<section class="students">
  <h2 class="section-title">For Students</h2>
  <p style="top:122px">Practice sets and study guides are built to match each exam. Every topic has been reviewed by our team of working instructors.</p>
  <p style="top:178px">When a new exam objective is released we update our material quickly, so you always study the current version and never waste time on old content.</p>
  <a class="btn" style="left:390px;width:204px">Practice Exams</a>
  <a class="btn" style="left:616px;width:197px">Exam Vouchers</a>
  <div class="photo" role="img" aria-label="Group of students gathered around a laptop"></div>
</section>

<section class="articles">
  <h2 class="section-title">Articles</h2>
  <article class="feature-post">
    <div class="thumb" role="img" aria-label="Laptop on a desk showing an online learning screen"></div>
    <h4>Continual Service Improvement Model</h4>
    <span class="date"><svg width="14" height="14" viewBox="0 0 24 24"><rect x="3" y="5" width="18" height="16" rx="2" fill="none" stroke="#fff" stroke-width="2"/><path d="M3 10h18M8 3v4M16 3v4" stroke="#fff" stroke-width="2"/></svg>March 8, 2018</span>
    <p>The final improvement model covered by the ServiceCore v3 Foundations exam is called the Continual...</p>
    <span class="more">More</span>
  </article>
  <div class="post" style="top:132px"><div class="day"><b>15</b><small>Feb</small></div><h4>Conclusion</h4><p>At this point, we have covered everything you need to know in order to take...</p></div>
  <div class="post" style="top:241px"><div class="day"><b>13</b><small>Feb</small></div><h4>Role of Automation in ServiceCore</h4><p>Unfortunately, humans can only focus on a few factors at once when making a decision.</p></div>
  <div class="post" style="top:344px"><div class="day"><b>06</b><small>Feb</small></div><h4>Deming Cycle</h4><p>While the ServiceCore v3 Foundations requires you to memorize the 7-Step Process Improvement</p></div>
  <div class="post" style="top:447px"><div class="day"><b>01</b><small>Feb</small></div><h4>7-Step Process Improvement Pro</h4><p>The 7-Step Process Improvement Process forms the core of the Continual Service Improvement</p></div>
  <svg class="next" width="40" height="22" viewBox="0 0 40 22"><path d="M0 11h34M26 3l8 8-8 8" stroke="#2c5687" stroke-width="3.5" fill="none"/></svg>
</section>

<section class="stats" role="region" aria-label="Figures over a dimmed photo of a person typing">
  <div class="stat" style="left:175px"><div class="icon"><svg width="40" height="40" viewBox="0 0 40 40"><circle cx="20" cy="20" r="16" fill="none" stroke="#fff" stroke-width="2.5"/><path d="M4 20h32M20 4c-8 9-8 23 0 32M20 4c8 9 8 23 0 32" stroke="#fff" stroke-width="2" fill="none"/></svg></div><b>30,000+</b><span>Students Worldwide</span></div>
  <div class="stat" style="left:416px"><div class="icon"><svg width="40" height="34" viewBox="0 0 40 34"><rect x="2" y="2" width="36" height="26" rx="2" fill="none" stroke="#fff" stroke-width="2.5"/><path d="M16 9v12l10-6z" fill="#fff"/></svg></div><b>1,000,000+</b><span>Minutes Watched</span></div>
  <div class="stat" style="left:625px"><div class="icon"><svg width="34" height="40" viewBox="0 0 34 40"><rect x="3" y="3" width="28" height="34" rx="2" fill="none" stroke="#fff" stroke-width="2.5"/><path d="M9 11h16M9 18h16" stroke="#fff" stroke-width="2"/></svg></div><b>5,000+</b><span>Book Sold</span></div>
  <div class="stat" style="left:884px"><div class="icon"><svg width="40" height="34" viewBox="0 0 40 34"><rect x="2" y="2" width="30" height="30" rx="2" fill="none" stroke="#fff" stroke-width="2.5"/><path d="M8 10h18M8 17h18M8 24h12" stroke="#fff" stroke-width="2"/></svg></div><b>1K+</b><span>Person Read the Blog</span></div>
</section>

<section class="books">
  <h2 class="section-title">Books</h2>
  <div class="book-cover" role="img" aria-label="Cover of the Quiz Brightly ServiceCore Foundation study book"></div>
  <div class="book-info">
    <h3>ServiceCore Foundation</h3>
    <p>Now available on Brixly in paperback and eBook formats!</p>
    <span class="store">Brixly</span>
    <a class="btn">Book Now</a>
  </div>
</section>

<section class="member">
  <h2 class="section-title">Become a Member</h2>
  <p style="top:140px">Join thousands of students who received our FREE eBook of ServiceCore v3 Foundations (Quiz Brightly) delivered right to your inbox and an exclusive special price on our video course!</p>
  <div class="signup"><span>Enter Email *</span><span class="go"><svg width="18" height="16" viewBox="0 0 18 16"><path d="M1 8 17 1l-4 14-4-5z" fill="#fff"/></svg></span></div>
  <p style="top:290px;font-size:13px;line-height:21px">By subscribing to QUIZ BRIGHTLY mailer, you will receive a free eBook sample version of the ServiceCore v3 Foundations (Quiz Brightly) book with over 50 pages of excellent content including a free full practice test.</p>
</section>

<footer class="site-footer">
  <div class="logo"><div class="mark"></div><div class="brand">Velmor<br>Academy</div></div>
  <div class="copy">© VELMOR ACADEMY - 2018 All<br>Right Reserved</div>
  <div class="foot-col" style="left:344px">
    <h4>Sitemap</h4>
    <ul><li>Start Here</li><li>Courses</li><li>Labs</li><li>Practice Exams</li><li>Exams Vouchers</li><li>Book</li><li>Articles</li><li>About Us</li></ul>
  </div>
  <div class="foot-col" style="left:609px">
    <h4>Contact Us</h4>
    <div class="contact-line"><svg width="14" height="18" viewBox="0 0 14 18"><path d="M7 0a7 7 0 0 0-7 7c0 5 7 11 7 11s7-6 7-11a7 7 0 0 0-7-7zm0 10a3 3 0 1 1 0-6 3 3 0 0 1 0 6z" fill="#5f8fc2"/></svg><span>Quiz Brightly<br>Larkfield, MD 20160</span></div>
    <div class="contact-line"><svg width="16" height="12" viewBox="0 0 16 12"><rect x="1" y="1" width="14" height="10" fill="none" stroke="#5f8fc2" stroke-width="1.6"/><path d="M1 1l7 6 7-6" stroke="#5f8fc2" stroke-width="1.6" fill="none"/></svg><span>info@quizbrightly.com</span></div>
    <div class="socials"><i></i><i></i><i></i></div>
  </div>
  <div class="foot-col" style="left:875px">
    <h4>Keep in Touch</h4>
    <p>We are looking forward to hearing from you. Please feel free to get in touch via the form below, we will get back to you as soon as possible.</p>
    <a class="btn">Contact Us</a>
  </div>
</footer>

</body>
</html>
```